I am a general contractor in Portland, Or. I would like a clean and simple design layout, maybe using the "didot" font, blue and dark bronze in colors are preferred. On one side of the card, it would be nice to have a logo(attached photo) and business name(KTW Construction). I don't need my job title on the card, just some thing along the lines of "gordon pike, general contractor". Thanks much.

Target Market(s)

Adults from 30-55 years old. Middle to upper class.

Industry/Entity Type

Contractor

Contact Information for Business Card

KTW Construction
Gordon L. Pike
2843 NE 71st Ave.
Portland, Or. 97288
541.555.0187

Font styles to use
Other font styles liked:
• didot

Colors
3277b5
7f7f7f

Requirements
Should not have
• Too much going on.

```html
<!DOCTYPE html>
<html lang="en">
<head>
<meta charset="utf-8">
<title>KTW Construction — Business Card</title>
<link rel="stylesheet" href="https://fonts.googleapis.com/css2?family=Exo+2:wght@400;500;700&display=swap">
<style>
  :root {
    --page: #ecebe8;
    --paper: #ffffff;
    --charcoal: #232323;
    --charcoal-soft: #2c3640;
    --sky: #1aa3e4;
    --ink-light: #ffffff;
    --card-w: 760px;
    --card-h: 434px;
  }
  * { box-sizing: border-box; margin: 0; padding: 0; }
  html, body {
    width: 1200px; height: 1018px; overflow: hidden;
    background: var(--page);
    font-family: "Exo 2", "Helvetica Neue", Arial, sans-serif;
  }
  .sheet {
    width: 1200px; height: 1018px;
    display: flex; flex-direction: column; align-items: center; justify-content: center;
    gap: 60px;
  }
  .card {
    position: relative;
    width: var(--card-w); height: var(--card-h);
    overflow: hidden;
    box-shadow: 0 6px 22px rgba(0,0,0,.18);
  }

  /* Front */
  .front { background: var(--paper); }
  .front__brand {
    position: absolute; left: 0; top: 0; right: 0; height: 232px;
    display: flex; align-items: center; gap: 22px;
    padding-left: 58px;
  }
  .brand-mark {
    width: 84px; height: 84px; border-radius: 50%;
    border: 8px solid var(--charcoal);
  }
  .brand-name {
    font-size: 44px; font-weight: 500; color: var(--sky); letter-spacing: .5px;
  }
  .front__contact {
    position: absolute; left: 0; right: 0; top: 232px; height: 108px;
    background: var(--charcoal);
    display: grid; grid-template-columns: 190px 1fr; grid-template-rows: 1fr 1fr;
    align-items: center; padding: 16px 0 16px 40px;
    color: var(--ink-light); font-size: 17px; letter-spacing: .4px;
  }
  .contact-item { display: flex; align-items: center; gap: 10px; }
  .contact-item svg { width: 16px; height: 16px; fill: var(--ink-light); flex: none; }
  .front__identity {
    position: absolute; left: 0; right: 0; bottom: 0; height: 94px;
    background: var(--sky); color: var(--ink-light);
    display: flex; justify-content: space-between; align-items: center;
    padding: 0 34px 0 40px;
  }
  .person-name { font-size: 30px; font-weight: 700; text-transform: uppercase; line-height: 1; }
  .person-role { font-size: 16px; font-weight: 400; text-transform: uppercase; letter-spacing: 1px; margin-top: 6px; }
  .address { text-align: right; font-size: 20px; font-weight: 500; line-height: 1.35; }

  /* Back */
  .back {
    background: linear-gradient(160deg, var(--charcoal) 0%, var(--charcoal) 45%, var(--charcoal-soft) 75%, #1f5f85 100%);
  }
</style>
</head>
<body>
<main class="sheet">
  <section class="card front" aria-label="Card front">
    <div class="front__brand">
      <span class="brand-mark" aria-hidden="true"></span>
      <span class="brand-name">KTW Construction</span>
    </div>
    <div class="front__contact">
      <div class="contact-item">
        <svg viewBox="0 0 16 16" aria-hidden="true"><path d="M3.6 1.2l2.3 2.6-1.2 1.9c.9 2 2.4 3.5 4.4 4.5l1.9-1.2 2.6 2.3-1.4 2.3C7.4 13.5 2.5 8.6 1.3 2.6z"/></svg>
        <span>541.555.0187</span>
      </div>
      <div class="contact-item">
        <svg viewBox="0 0 16 16" aria-hidden="true"><path d="M1 3h14v10H1zm1.5 1.3v.3L8 8.6l5.5-4v-.3zm0 2v5.4h11V6.3L8 10.3z"/></svg>
        <span>gordon@ktwbuild.com</span>
      </div>
      <div class="contact-item">
        <svg viewBox="0 0 16 16" aria-hidden="true"><path d="M4 1h8v14H4zm1.5 1.5v9.5h5V2.5zM7 13h2v1H7z"/></svg>
        <span>541.555.0142</span>
      </div>
      <div class="contact-item">
        <svg viewBox="0 0 16 16" aria-hidden="true"><circle cx="8" cy="8" r="6.5" fill="none" stroke="#fff" stroke-width="1.4"/><path d="M1.5 7.3h13v1.4h-13zM7.3 1.5h1.4v13H7.3z"/></svg>
        <span>www.ktwbuild.com</span>
      </div>
    </div>
    <div class="front__identity">
      <div class="person">
        <p class="person-name">Gordon Pike</p>
        <p class="person-role">General Contractor</p>
      </div>
      <p class="address">2843 NE 71st Ave.<br>Portland, Or. 97288</p>
    </div>
  </section>

  <section class="card back" role="img" aria-label="Card back: geometric pattern in charcoal and blue"></section>
</main>
</body>
</html>
```